Maple Grove Schools | brand new stationery!

We need stationery design with our new logo! Our company updated it's name and image and we like to incorporate the new one on our stationery, business cards and email signature. We are looking for fresh, new ideas!
Industry: Childcare, Elementary and Middle School
Company Name: Maple Grove Schools
Tagline: Bright Futures Start Here
Main colors: Blue, white and a little yellow
Star shape is something new for us! Do you see a way to incorporate it as a design element?

```html
<!DOCTYPE html>
<html lang="en">
<head>
<meta charset="utf-8">
<title>Maple Grove Schools – Stationery</title>
<link href="https://fonts.googleapis.com/css2?family=Outfit:wght@400;600&family=Roboto+Condensed:wght@400&display=swap" rel="stylesheet">
<style>
  :root{
    --navy:#0b1a6f;
    --yellow:#fbbd17;
    --ink:#231f20;
    --paper:#ffffff;
    --backdrop:#e4e5e7;
  }
  *{margin:0;padding:0;box-sizing:border-box}
  html,body{width:1200px;height:832px;overflow:hidden}
  body{background:var(--backdrop);position:relative;font-family:'Outfit',sans-serif;color:var(--ink)}
  .sheet{position:absolute;background:var(--paper);overflow:hidden;box-shadow:0 4px 8px rgba(0,0,0,.18)}
  .brand{position:absolute;text-align:center;font-weight:600;line-height:1.02;color:var(--ink)}
  .brand span{display:block}
  .brand-dot{position:absolute;border-radius:50%;background:var(--navy)}
  .corner-shape{position:absolute;border-radius:50%;background:var(--navy)}
  .contacts{position:absolute;border-left:1.5px solid var(--yellow);list-style:none}
  .contacts li{display:flex;align-items:center;white-space:nowrap}
  .contacts .icon{border-radius:50%;background:var(--yellow);flex:none}
  .person-name{position:absolute;color:var(--navy);font-weight:600;white-space:nowrap}
  .person-role{position:absolute;white-space:nowrap}

  /* business card front */
  .card-front{left:60px;top:70px;width:270px;height:162px;background:var(--navy)}
  .card-front .brand{left:22px;top:44px;width:112px;color:#fff;font-size:19px}
  .card-front .corner-shape{left:160px;top:30px;width:170px;height:170px;background:#fff}
  .tagline{position:absolute;left:22px;top:134px;font-family:'Roboto Condensed',sans-serif;font-size:9px;color:var(--yellow);letter-spacing:.1px}

  /* business card back */
  .card-back{left:355px;top:70px;width:270px;height:162px}
  .card-back .brand-dot{left:46px;top:22px;width:20px;height:20px}
  .card-back .brand{left:14px;top:50px;width:84px;font-size:12.5px}
  .card-back .person-name{left:19px;top:92px;font-size:10.5px}
  .card-back .person-role{left:19px;top:105px;font-size:6.5px}
  .card-back .contacts{left:19px;top:117px;padding-left:3px;font-size:6px}
  .card-back .contacts li{height:9.3px;gap:2px}
  .card-back .contacts .icon{width:5px;height:5px}
  .card-back .corner-shape{left:150px;top:30px;width:170px;height:170px}

  /* email signature */
  .signature{left:61px;top:279px;width:564px;height:143px}
  .signature .brand-dot{left:62px;top:34px;width:22px;height:22px}
  .signature .brand{left:14px;top:73px;width:120px;font-size:19px}
  .sig-rule{position:absolute;left:144px;top:32px;width:1.5px;height:28px;background:var(--navy)}
  .signature .person-name{left:150px;top:29px;font-size:17.5px}
  .signature .person-role{left:150px;top:49px;font-size:11px}
  .signature .contacts{left:144px;top:72px;padding-left:5px;font-size:11px}
  .signature .contacts li{height:15.6px;gap:4px}
  .signature .contacts .icon{width:8px;height:8px}
  .signature .corner-shape{left:440px;top:20px;width:170px;height:170px}

  /* envelope */
  .envelope{left:59px;top:478px;width:566px;height:284px}
  .envelope .brand-dot{left:60px;top:20px;width:22px;height:22px}
  .envelope .brand{left:16px;top:59px;width:106px;font-size:18px}
  .address{position:absolute;left:18px;top:99px;font-size:6.5px;white-space:nowrap}
  .envelope .corner-shape{left:410px;top:120px;width:220px;height:220px}

  /* letterhead */
  .letterhead{left:648px;top:68px;width:497px;height:696px}
  .letterhead .brand-dot{left:60px;top:26px;width:24px;height:24px}
  .letterhead .brand{left:18px;top:62px;width:108px;font-size:19.5px}
  .letterhead .contacts{left:20px;top:642px;padding-left:5px;font-size:9px}
  .letterhead .contacts li{height:12.6px;gap:3px}
  .letterhead .contacts .icon{width:7px;height:7px}
  .letterhead .corner-shape{left:350px;top:560px;width:210px;height:210px}
</style>
</head>
<body>

<section class="sheet card-front" aria-label="Business card front">
  <div class="brand"><span>Maple Grove</span><span>Schools</span></div>
  <p class="tagline">BRIGHT FUTURES START HERE</p>
  <div class="corner-shape" role="img" aria-label="Large brand decoration"></div>
</section>

<section class="sheet card-back" aria-label="Business card back">
  <div class="brand-dot"></div>
  <div class="brand"><span>Maple Grove</span><span>Schools</span></div>
  <p class="person-name">JANE MILLER</p>
  <p class="person-role">Manager</p>
  <ul class="contacts">
    <li><i class="icon"></i>(+61) 190055512</li>
    <li><i class="icon"></i>info@maplegroveschool.com</li>
    <li><i class="icon"></i>www.maplegroveschool.com</li>
  </ul>
  <div class="corner-shape" role="img" aria-label="Large brand decoration"></div>
</section>

<section class="sheet signature" aria-label="Email signature">
  <div class="brand-dot"></div>
  <div class="brand"><span>Maple Grove</span><span>Schools</span></div>
  <div class="sig-rule"></div>
  <p class="person-name">JANE MILLER</p>
  <p class="person-role">Manager</p>
  <ul class="contacts">
    <li><i class="icon"></i>(+61) 190055512</li>
    <li><i class="icon"></i>info@maplegroveschool.com</li>
    <li><i class="icon"></i>www.maplegroveschool.com</li>
  </ul>
  <div class="corner-shape" role="img" aria-label="Large brand decoration"></div>
</section>

<section class="sheet envelope" aria-label="Envelope">
  <div class="brand-dot"></div>
  <div class="brand"><span>Maple Grove</span><span>Schools</span></div>
  <p class="address">Your address, your city, box 88900</p>
  <div class="corner-shape" role="img" aria-label="Large brand decoration"></div>
</section>

<section class="sheet letterhead" aria-label="Letterhead">
  <div class="brand-dot"></div>
  <div class="brand"><span>Maple Grove</span><span>Schools</span></div>
  <ul class="contacts">
    <li><i class="icon"></i>(+61) 190055512</li>
    <li><i class="icon"></i>info@maplegroveschool.com</li>
    <li><i class="icon"></i>www.maplegroveschool.com</li>
  </ul>
  <div class="corner-shape" role="img" aria-label="Large brand decoration"></div>
</section>

</body>
</html>
```